Velmora Freightway Solutions Business cards

Would like a very unique design catchy but professional for business cards. Please use log provided.Marlon WellsCeo and Founder TransCon Logistix Solutions1-888-913-3225mwells@tlsolutionsus.comwww.tlsolutionsus.com

```html
<!DOCTYPE html>
<html lang="en">
<head>
<meta charset="utf-8">
<title>Velmora Freightway Solutions – Business Cards</title>
<link rel="stylesheet" href="https://fonts.googleapis.com/css2?family=Montserrat:wght@500;600;700&display=swap">
<style>
  :root {
    --brand-blue: #1b78bf;
    --brand-red: #e8232b;
    --card-white: #ffffff;
    --backdrop: #ecebe8;
    --text-blue: #1c74bb;
  }
  * { margin: 0; padding: 0; box-sizing: border-box; }
  html, body {
    width: 1200px; height: 831px; overflow: hidden;
    background: var(--backdrop);
    font-family: "Montserrat", Arial, sans-serif;
  }
  .sheet {
    position: relative; width: 1200px; height: 831px;
    display: flex; align-items: center; justify-content: center; gap: 40px;
  }
  .card {
    position: relative; width: 540px; height: 309px; overflow: hidden;
    box-shadow: 0 6px 18px rgba(0,0,0,0.18);
  }
  /* Back side */
  .card--back {
    background: var(--brand-blue);
    display: flex; align-items: center; justify-content: center;
  }
  .brand-lockup { display: flex; align-items: center; gap: 12px; }
  .brand-lockup__mark { width: 18px; height: 18px; background: var(--card-white); }
  .brand-lockup__name {
    color: var(--card-white); font-weight: 700; font-size: 22px;
    letter-spacing: 0.5px; line-height: 1.2; text-transform: uppercase;
  }
  /* Front side */
  .card--front { background: var(--card-white); }
  .holder { position: absolute; left: 44px; top: 62px; }
  .holder__name {
    font-size: 27px; font-weight: 600; letter-spacing: 0.5px;
    text-transform: uppercase; color: var(--text-blue); line-height: 1.2;
  }
  .holder__name .surname { color: var(--brand-red); }
  .holder__title { margin-top: 2px; font-size: 13px; font-weight: 500; color: var(--brand-red); }
  .divider {
    position: absolute; left: 44px; top: 128px; width: 446px; height: 2px;
    background: var(--brand-blue);
  }
  .contact { position: absolute; left: 44px; top: 142px; list-style: none; }
  .contact__item {
    display: flex; align-items: center; gap: 8px;
    font-size: 15px; font-weight: 500; color: var(--text-blue); margin-bottom: 8px;
  }
  .contact__item svg { width: 13px; height: 13px; flex: none; }
  .company-name {
    position: absolute; right: 36px; top: 58px; width: 200px; text-align: right;
    font-size: 15px; font-weight: 700; line-height: 1.25; text-transform: uppercase;
    color: var(--text-blue);
  }
  .footer-band { position: absolute; left: 0; bottom: 0; width: 540px; height: 80px; display: block; }
  .website {
    position: absolute; right: 28px; bottom: 12px; line-height: 1;
    font-size: 15px; font-weight: 600; color: var(--card-white); letter-spacing: 0.3px;
  }
</style>
</head>
<body>
<main class="sheet">
  <section class="card card--back" aria-label="Card back">
    <div class="brand-lockup">
      <span class="brand-lockup__mark"></span>
      <span class="brand-lockup__name">Velmora Freightway<br>Solutions</span>
    </div>
  </section>

  <section class="card card--front" aria-label="Card front">
    <div class="holder">
      <h1 class="holder__name">Dorian <span class="surname">Pike</span></h1>
      <p class="holder__title">Ceo and Founder</p>
    </div>
    <div class="divider"></div>
    <ul class="contact">
      <li class="contact__item">
        <svg viewBox="0 0 24 24"><path fill="#e8232b" d="M6.6 10.8a15 15 0 0 0 6.6 6.6l2.2-2.2a1 1 0 0 1 1-.25 11.4 11.4 0 0 0 3.6.57 1 1 0 0 1 1 1V20a1 1 0 0 1-1 1A17 17 0 0 1 3 4a1 1 0 0 1 1-1h3.5a1 1 0 0 1 1 1c0 1.25.2 2.45.57 3.57a1 1 0 0 1-.25 1z"/></svg>
        1-888-470-6158
      </li>
      <li class="contact__item">
        <svg viewBox="0 0 24 24"><rect x="2" y="5" width="20" height="14" fill="#e8232b"/><path d="M2 5l10 8 10-8" fill="none" stroke="#fff" stroke-width="2"/></svg>
        dpike@vfwayroutes.com
      </li>
    </ul>
    <p class="company-name">Velmora Freightway Solutions</p>

    <svg class="footer-band" viewBox="0 0 540 80" aria-hidden="true">
      <polygon points="0,0 276,38 276,42 0,4" fill="#1b78bf"/>
      <polygon points="0,14 282,52 282,60 0,22" fill="#e8232b"/>
      <polygon points="0,30 280,66 300,42 540,42 540,80 0,80" fill="#1b78bf"/>
    </svg>
    <p class="website">www.vfwayroutes.com</p>
  </section>
</main>
</body>
</html>
```